Stationery Design Task - Stationary, memo and report templates for professional services company

Looking for someone to update stationary design but just as importantly come up with a template for reports and memos for use in our consulting firm. Would also like some brand use guidelines to be able to share with our whole team. We have an existing logo that we like. Need to update with a more contemporary look so that our deliverables to clients look good and professional yet stylish. This is for business to business communications. No need for envelope design. Important to have design for multiple pages, i.e. first page of a report and then 2nd page. Need to use in MS word documents so must be easy to use and replicate. Don't want something overly complex. Clean, fresh looking is best.

Industry/Entity Type

Information Technology

Font styles to use
Sans Serif

Colors
33a6d7
0792cd
85cae6
cee9f5
cedeed
85abd2
3377b5
0455a3

Requirements
Must have
• Clean look but with a little style or pop. Something that can easily be used in word documents. Need to have page styles that have a first page of a report (not a cover page) and then secondary page.
Nice to have
• - Although the dark blue is our primary color. Might be willing to look at some accent color as well.
Should not have
• Not just our logo on the page with a color bar.

```html
<!DOCTYPE html>
<html lang="en">
<head>
<meta charset="utf-8">
<title>Northvale Systems Letterhead</title>
<link href="https://fonts.googleapis.com/css2?family=Open+Sans:wght@400;700&display=swap" rel="stylesheet">
<style>
  :root {
    --backdrop: #d9d9d9;
    --paper: #ffffff;
    --brand-blue: #0a72c4;
    --sky: #daeaf6;
    --swoosh-grey: #d6d6d6;
    --watermark: #efefef;
    --tab-grey: #cfcfcf;
    --ink-grey: #6b6b6b;
  }
  * { margin: 0; padding: 0; box-sizing: border-box; }
  html, body {
    width: 1200px; height: 784px; overflow: hidden;
    background: var(--backdrop);
    font-family: "Open Sans", sans-serif;
  }
  .letterhead {
    position: absolute; left: 345px; top: 32px;
    width: 509px; height: 720px;
    background: var(--paper);
    box-shadow: 0 6px 18px rgba(0,0,0,0.18);
    overflow: hidden;
  }
  .letterhead-art { position: absolute; inset: 0; }
  .brand-name {
    position: absolute; left: 34px; top: 26px;
    display: flex; align-items: center; gap: 7px;
    color: var(--brand-blue);
    font-weight: 700; font-size: 19px; letter-spacing: 0.5px;
    text-transform: uppercase; line-height: 1;
  }
  .brand-dot {
    width: 14px; height: 14px; border-radius: 50%;
    background: var(--brand-blue);
  }
  .contact-line {
    position: absolute; left: 12px; top: 682px;
    display: flex; align-items: center; gap: 4px;
    font-size: 8.2px; color: var(--ink-grey); white-space: nowrap;
  }
  .contact-icon {
    display: inline-block; width: 8px; height: 8px; border-radius: 50%;
    background: var(--brand-blue); margin-right: 3px; flex: none;
  }
  .contact-line .item { display: inline-flex; align-items: center; }
  .web-address {
    position: absolute; right: 10px; top: 708px;
    display: flex; align-items: center;
    font-size: 8.2px; line-height: 1; color: var(--ink-grey); white-space: nowrap;
  }
</style>
</head>
<body>
  <main class="letterhead">
    <svg class="letterhead-art" width="509" height="720" viewBox="0 0 509 720" aria-hidden="true">
      <path d="M150 0 C 250 40, 300 110, 360 165 C 410 208, 460 226, 509 232 L 509 0 Z" fill="var(--sky)"/>
      <path d="M178 0 C 268 40, 312 105, 372 158 C 418 198, 462 214, 509 220" fill="none" stroke="#ffffff" stroke-width="5"/>
      <path d="M110 16 C 190 40, 235 90, 262 140 C 240 98, 190 52, 110 22 Z" fill="var(--swoosh-grey)"/>
      <rect x="0" y="0" width="6" height="22" fill="var(--brand-blue)"/>
      <rect x="6" y="0" width="22" height="6" fill="var(--tab-grey)"/>
      <rect x="501" y="226" width="8" height="12" fill="var(--brand-blue)"/>
      <rect x="495" y="238" width="14" height="6" fill="var(--tab-grey)"/>
      <rect x="0" y="700" width="385" height="6" fill="var(--brand-blue)"/>
      <rect x="385" y="706" width="16" height="14" fill="var(--tab-grey)"/>
    </svg>

    <div role="img" aria-label="Faint grey brand decoration" style="position:absolute;left:30px;top:190px;width:290px;height:300px;border-radius:50%;background:radial-gradient(circle at 50% 50%, var(--watermark) 0%, var(--watermark) 55%, rgba(239,239,239,0) 72%);"></div>

    <div class="brand-name"><span class="brand-dot"></span>Northvale Systems</div>

    <div class="contact-line">
      <span class="item"><span class="contact-icon"></span>0000 Sample Street, Lakeview, NZ00000</span>
      <span class="item"><span class="contact-icon"></span>(000) 555 0142</span>
      <span class="item"><span class="contact-icon"></span>info@northvalesystems.com</span>
    </div>
    <div class="web-address"><span class="contact-icon"></span>www.northvalesystems.com</div>
  </main>
</body>
</html>
```